Hearthside Lending Relief

Please help us give our website a remake or a FACELIFT. It is not very good but it says what we need it to say. But the design is terrible.
I would like our new design font and logo to be used as the theme.

I also want more photos on the site.

I also want consistency with the pages so they look clean.

We want the professionals to do this, let's see what you got!

Thank you!
Updates

Project Deadline Extended
Reason: I can understand you want to be paid. So I will commit to the fee but I want you to have time to make a KICK ASS website for me dudes! Thanks

HI!  Just wanted to say thanks for your time on these.  A lot are great.  However the firefighters have nothing to do with Foreclosure.  We are saving peoples homes from the bank taking them and selling them.   I LOVE the house photos and the families on the website.  That is the direction we like.  THanks.

THANK U ALL FOR THE WORK!   I like a few ending in the numbers: 147  733  693  536  620  478  727  508     I will go over them and choose one soon.  Thank you.   You will be paid shortly. 

Requirements
Must have
• Bright, Upbeat photos. Color scheme should be in order. We like icons on the bottom. not just text.

```html
<!DOCTYPE html>
<html lang="en">
<head>
<meta charset="utf-8">
<title>Hearthside Lending Relief</title>
<link href="https://fonts.googleapis.com/css2?family=Arimo:wght@400;700&family=Tinos&display=swap" rel="stylesheet">
<style>
:root{
  --red:#e3262b;
  --blue-link:#1f8ccc;
  --phone-blue:#1a86c9;
  --body-bg:#ebecee;
  --text:#5a5a5a;
  --text-dark:#444;
  --rule:#cfd1d4;
  --nav-top:#6a6b6d;
  --nav-bottom:#3d3e40;
  --footer-top:#0d4f8c;
  --footer-bottom:#06244a;
  --footer-head:#3aa3e6;
}
*{box-sizing:border-box;margin:0;padding:0}
html,body{width:815px;height:1200px;overflow:hidden}
body{position:relative;background:#fff;font-family:"Arimo",Arial,sans-serif;color:var(--text)}
.abs{position:absolute}

/* header */
.header{left:0;top:0;width:815px;height:147px;background:#fff}
.account-tab{left:621px;top:0;width:88px;height:19px;background:#e2e3e5;font-size:8px;color:#777;display:flex;align-items:center;justify-content:center;gap:4px}
.brand{left:116px;top:40px;display:flex;align-items:center;gap:8px}
.brand-mark{width:44px;height:44px;border-radius:50%;background:var(--red)}
.brand-name{font-weight:700;font-size:15px;line-height:16px;color:var(--red);text-transform:uppercase;letter-spacing:.3px;width:160px}
.callout{left:456px;top:60px;display:flex;align-items:baseline;gap:7px}
.callout-label{font-size:12px;color:#555}
.callout-phone{font-family:"Tinos",serif;font-size:27px;color:var(--phone-blue)}
.nav{left:105px;top:105px;width:604px;height:31px;background:linear-gradient(var(--nav-top),var(--nav-bottom));display:flex;align-items:center;border-radius:2px}
.nav-item{height:31px;display:flex;align-items:center;justify-content:center;color:#eee;font-size:11px;border-right:1px solid #2e2f30;text-transform:uppercase}
.nav-item.active{background:#4a4b4d}
.search{margin-left:10px;width:122px;height:19px;background:#fff;display:flex;align-items:center;justify-content:space-between;font-size:8px;color:#999;padding-left:6px}
.search-btn{width:18px;height:19px;background:var(--red);display:flex;align-items:center;justify-content:center}

/* body */
.main{left:0;top:147px;width:815px;height:838px;background:var(--body-bg)}
.section-title{font-family:"Tinos",serif;font-variant:small-caps;color:var(--red);font-size:19px;letter-spacing:.5px;border-bottom:1px solid var(--rule);padding-bottom:2px}
.feature-photo{width:176px;height:114px}
.feature-text{width:181px;font-size:8.7px;line-height:14.4px;text-align:justify}
.feature-text b,.about-text b{color:var(--text-dark)}
.about-text{left:105px;top:646px;width:268px;font-size:9.8px;line-height:18.3px;text-align:justify}
.solution-photo{left:438px;width:106px}
.solution-list{left:564px;top:652px;list-style:none;font-size:9px;color:var(--blue-link)}
.solution-list li{height:20.4px;display:flex;gap:9px}
.solution-list li::before{content:"»";color:var(--red)}
.solution-list li.gap{height:20.4px}
.solution-list li.gap::before{content:""}
.solution-list li.cont::before{color:transparent}

/* footer */
.footer{left:0;top:985px;width:815px;height:215px;background:radial-gradient(ellipse at 45% 0%,var(--footer-top),var(--footer-bottom) 80%)}
.footer-col{top:1027px}
.footer-col h3{font-size:13px;color:var(--footer-head);margin-bottom:3px}
.footer-col a{display:block;font-size:7.5px;color:#e6eef7;text-decoration:none;line-height:13px}
.newsletter-title{left:379px;top:1027px;font-size:13px;font-weight:700;color:#fff}
.email{left:377px;top:1054px;width:150px;height:23px;background:#fff;border-radius:3px;font-size:8.5px;color:#888;display:flex;align-items:center;padding-left:9px}
.subscribe{left:535px;top:1054px;width:75px;height:23px;background:var(--red);border-radius:3px;color:#fff;font-weight:700;font-size:10.5px;display:flex;align-items:center;justify-content:center}
.social{left:642px;top:1055px;display:flex;gap:3px}
.social span{width:21px;height:21px;border-radius:3px;background:#d9dde2}
.footer-rule{left:0;top:1127px;width:815px;height:1px;background:#1e4f80}
.legal{left:119px;top:1150px;font-size:7.5px;color:#e6eef7}
.copyright{left:119px;top:1163px;font-size:7.5px;color:var(--footer-head);letter-spacing:.2px}
</style>
</head>
<body>

<header class="abs header"></header>
<div class="abs account-tab"><span>Login</span><span>|</span><span>Contacts</span></div>

<div class="abs brand">
  <span class="brand-mark"></span>
  <span class="brand-name">Hearthside Lending Relief</span>
</div>

<div class="abs callout">
  <span class="callout-label">Call Toll-Free Now</span>
  <span class="callout-phone">877-555-0148</span>
</div>

<nav class="abs nav">
  <div class="nav-item" style="width:74px">
    <svg width="16" height="14" viewBox="0 0 16 14"><path d="M8 0L0 7h2v7h4V9h4v5h4V7h2z" fill="#fff"/></svg>
  </div>
  <div class="nav-item" style="width:80px">About Us</div>
  <div class="nav-item active" style="width:86px">Services</div>
  <div class="nav-item" style="width:136px">Financing Options</div>
  <div class="nav-item" style="width:96px;border-right:none">Contact Us</div>
  <div class="search"><span>Search...</span>
    <span class="search-btn"><svg width="10" height="10" viewBox="0 0 10 10"><circle cx="4" cy="4" r="3" stroke="#fff" stroke-width="1.4" fill="none"/><path d="M6 6l3.5 3.5" stroke="#fff" stroke-width="1.6"/></svg></span>
  </div>
</nav>

<main class="abs main"></main>

<h2 class="abs section-title" style="left:105px;top:188px;width:604px">Featured Services Overview</h2>

<div class="abs feature-photo" style="left:105px;top:243px;background:linear-gradient(135deg,#3c3f3a,#d83a2c 45%,#6f8f3a)" role="img" aria-label="Person holding a red home for sale foreclosure sign on a lawn"></div>
<div class="abs feature-photo" style="left:319px;top:243px;background:linear-gradient(135deg,#e9e6e0,#c9a98c 45%,#2f5c47)" role="img" aria-label="Smiling family with a young daughter and piggy bank meeting an advisor"></div>
<div class="abs feature-photo" style="left:535px;top:243px;background:linear-gradient(135deg,#c73b35,#e8e3df 50%,#2e2b2b)" role="img" aria-label="Handshake over a for sale sign marked sold"></div>

<p class="abs feature-text" style="left:105px;top:377px"><b>Lorem ipsum dolor sit amet, consectetur adipiscingsil elit.</b> Vestibulum vestibulum tincidunt orci, nec volutpatli dolor sollicitudin sed. Fusce temph or sodales massa ac cursus. Donec congue eleifejf rpnd est eu placerat. Suspendisse gravida turpis at metus placerat mattis. Phasellus tincidunt nisl at felis commodo lacinia nec vel quam. Proin auctor enim ipsum. Duis faucibus, ipsum ut ornare viverra, orci dolor mattis massa, ut scelerisque.</p>
<p class="abs feature-text" style="left:319px;top:377px"><b>Lorem ipsum dolor sit amet, consectetur adipiscingsil elit.</b> Vestibulum vestibulum tincidunt orci, nec volutpatli dolor sollicitudin sed. Fusce temph or sodales massa ac cursus. Donec congue eleifejf rpnd est eu placerat. Suspendisse gravida turpis at metus placerat mattis. Phasellus tincidunt nisl at felis commodo lacinia nec vel quam. Proin auctor enim ipsum. Duis faucibus, ipsum ut ornare viverra, orci dolor mattis massa, ut scelerisque.</p>
<p class="abs feature-text" style="left:533px;top:377px"><b>Lorem ipsum dolor sit amet, consectetur adipiscingsil elit.</b> Vestibulum vestibulum tincidunt orci, nec volutpatli dolor sollicitudin sed. Fusce temph or sodales massa ac cursus. Donec congue eleifejf rpnd est eu placerat. Suspendisse gravida turpis at metus placerat mattis. Phasellus tincidunt nisl at felis commodo lacinia nec vel quam. Proin auctor enim ipsum. Duis faucibus, ipsum ut ornare viverra, orci dolor mattis massa, ut scelerisque.</p>

<h2 class="abs section-title" style="left:105px;top:598px;width:268px">What We Do</h2>
<p class="abs about-text"><b>Lorem ipsum dolor sit amet, consectetur adipiscingsil elit. Vestibulum vestibulum tincidunt orci,</b> nec volutpatli dolor sollicitudin sed. Fusce temph or sodales massa ac cursus. Donec congue eleifejf rpnd est eu placerat. Suspendisse gravida turpis at metus. placerat mattis. Phasellus tincidunt nisl at felis commodo lacinia nec vel quam. Proin auctor enim ipsum. Duis faucibus, ipsum ut ornare viverra, orci dolor mattis massa, ut scelerisque augue mauris vel diam. Fusce temph or sodales massa ac cursus. Donec congue eleifejf rpnd est eu placerat. Suspendisse gravida turpis at metus placerat mattis. Phasellus tincidunt nisl at felis commodo lacinia nec vel quam. Proin auctor enim ipsum. Duis faucibus, ipsum ut ornare viverra, orci dolor mattis massa, ut scelerisque.</p>

<h2 class="abs section-title" style="left:438px;top:598px;width:267px">Professional Solutions</h2>
<div class="abs solution-photo" style="top:657px;height:69px;background:linear-gradient(135deg,#f0efec,#b9a08a 50%,#23303f)" role="img" aria-label="Couple shaking hands with a lending advisor"></div>
<div class="abs solution-photo" style="top:747px;height:70px;background:linear-gradient(135deg,#e9e6e0,#c9a98c 45%,#2f5c47)" role="img" aria-label="Family with a child meeting an advisor at a table"></div>
<div class="abs solution-photo" style="top:842px;height:68px;background:linear-gradient(#9dbad6,#8a8a78 45%,#5f9a3a)" role="img" aria-label="Family relaxing on the lawn in front of their house"></div>

<ul class="abs solution-list">
  <li>Donec porta diam eu massa</li>
  <li>Quisque diam lorem</li>
  <li>Interdum vitae,dapibus ac</li>
  <li>Scelerisque vitae, pede</li>
  <li>Donec eget tellus non erat</li>
  <li>Lacinia fermentum</li>
  <li class="gap"></li>
  <li>Tincidunt ac, viverra sed, nulla</li>
  <li>Donec porta diam eu massa</li>
  <li>Quisque diam loremInterdum</li>
  <li>vitae,dapibus acScelerisque</li>
  <li class="cont">vitae, pede</li>
  <li>Donec eget tellus non erat</li>
</ul>

<footer class="abs footer"></footer>

<div class="abs footer-col" style="left:119px"><h3>About Us</h3><a>Company Info</a><a>Our Services</a><a>Clients</a><a>Partners</a></div>
<div class="abs footer-col" style="left:218px"><h3>Advice</h3><a>Sign up</a><a>Forums</a><a>Promotion</a><a>Career</a></div>
<div class="abs footer-col" style="left:303px"><h3>Join In</h3><a>FAQs</a><a>Solutions</a><a>Sitemap</a><a>Contacts</a></div>

<div class="abs newsletter-title">Join our Newsletter</div>
<div class="abs email">Email Address:</div>
<div class="abs subscribe">Subscribe</div>
<div class="abs social"><span></span><span></span><span></span></div>

<div class="abs footer-rule"></div>
<div class="abs legal">Disclaimer &amp; Terms &amp; Conditions &nbsp;|&nbsp; Privacy Policy &nbsp;| Advertise With Us &nbsp;| &nbsp;Contact Us</div>
<div class="abs copyright">Hearthside Lending Relief &nbsp;© 2012. &nbsp;All Rights Reserved</div>

</body>
</html>
```